Tarvex Engineering Rail Sector Brochure

We need a new 3 page folding brochure for Tarvex Engineering Pty Ltd. The organisation is currently supporting customers in Defence, Maritime and Information and Communications Technology companies. We are currently looking to expand our engineering services into the rail sector by providing manpower and consultancy services to railway sector clients.We would like the brochure to be based on an A4 page and look technical with particular focus on communications systems used within the railways. This could include pictures of rail control centres, trains (Australian trains only please), train radio communications equipment, radio antennas, computers and networking equipment. Please use both graphics and photos.The brochure will be provided to potential rail customers and should be clear and uncluttered.The following is our company website: www.tarvexengineering.com.au if you would like more detail on our current work.I have attached the file for our logo which should appear on the brochure.
Target Market(s)
Providing manpower and consultancy services to the railway sector. This includes rail companies (e.g. Quillane Transit Lines, K/Rail etc) and rail equipment and carriage suppliers (e.g. Feltmark)
Colors
Designer to choose colors to be used in the design.
Requirements
Must have
- Instead of having "lorem ipsum" text in the brochure you can please use some of the text in the file we have provided. Not all has to be used, and you should not be limited to what is in the file.
Nice to have
- Mixture of different font sizes to highlight particular text elements.

```html
<!DOCTYPE html>
<html lang="en">
<head>
<meta charset="utf-8">
<title>Tarvex Engineering Rail Sector Brochure</title>
<link rel="stylesheet" href="https://fonts.googleapis.com/css2?family=Questrial&family=Didact+Gothic&display=swap">
<style>
  :root {
    --page-bg: #9a9a9a;
    --navy: #233f97;
    --royal: #2f58b8;
    --sky: #4d86d6;
    --yellow: #f2e21a;
    --white: #ffffff;
    --ink: #1f2233;
    --net-blue: #1e6fc4;
    --comm-blue: #2b3aa6;
    --cmd-violet: #5a2d9a;
    --sensor-magenta: #a0399c;
  }
  * { margin: 0; padding: 0; box-sizing: border-box; }
  html, body { width: 1200px; height: 800px; overflow: hidden; }
  body {
    background: radial-gradient(ellipse at center, #b5b5b5 0%, var(--page-bg) 100%);
    font-family: "Questrial", "Didact Gothic", sans-serif;
    position: relative;
  }
  .brochure {
    position: absolute; left: 60px; top: 18px;
    width: 1080px; height: 764px;
    display: flex;
    box-shadow: 0 12px 30px rgba(0,0,0,.35);
  }
  .panel { width: 360px; height: 764px; position: relative; overflow: hidden; }

  /* Left panel */
  .panel--intro {
    background: linear-gradient(180deg, var(--royal) 0%, var(--navy) 100%);
    color: var(--white);
    padding: 30px 28px 0 34px;
  }
  .headline { font-size: 25px; line-height: 1.12; font-weight: 400; }
  .headline strong { color: var(--yellow); font-weight: 700; }
  .headline .caps { color: var(--yellow); display: block; }
  .lead { font-size: 14.5px; line-height: 1.25; margin: 16px 0 22px; }
  .intro-copy { font-size: 9.6px; line-height: 1.4; margin-bottom: 14px; color: #e6ebfa; }
  .capabilities { list-style: none; font-size: 10.2px; line-height: 1.35; }
  .capabilities li { display: flex; gap: 10px; margin-bottom: 11px; }
  .capabilities svg { flex: 0 0 11px; margin-top: 2px; }
  .network-visual {
    position: absolute; left: 0; bottom: 0; width: 360px; height: 206px;
    background: radial-gradient(ellipse at 55% 40%, #bfe4ff 0%, #3a8fe0 30%, #12408f 70%, #0b2a66 100%);
  }

  /* Middle panel */
  .panel--services { background: var(--white); color: var(--ink); padding: 26px 28px 0 34px; }
  .services-intro { font-size: 10px; line-height: 1.4; }
  .chart { display: block; margin: 10px 0 8px; }
  .service-group { margin-bottom: 12px; }
  .service-title { font-size: 13.5px; font-weight: 700; margin-bottom: 4px; }
  .service-title--network { color: var(--net-blue); }
  .service-title--comms { color: var(--comm-blue); }
  .service-title--command { color: var(--cmd-violet); }
  .service-title--sensor { color: var(--sensor-magenta); }
  .service-list { list-style: none; font-size: 10.4px; line-height: 1.38; }

  /* Right panel */
  .panel--capability { background: var(--navy); }
  .tower-photo {
    position: absolute; left: 0; top: 0; width: 360px; height: 440px;
    background: linear-gradient(180deg, #3f7fd1 0%, #6ea6e4 45%, #a9cdf2 75%, #dbe9f7 100%);
  }
  .capability-band { position: absolute; left: 0; top: 380px; width: 360px; height: 384px; }
  .capability-copy {
    position: absolute; left: 30px; top: 440px; width: 300px;
    color: var(--yellow); font-size: 10.4px; line-height: 1.45;
  }
  .capability-copy p + p { margin-top: 12px; }
</style>
</head>
<body>
<main class="brochure">

  <section class="panel panel--intro">
    <h1 class="headline">A <strong>trusted</strong> provider<br>to the world’s most<span class="caps">EXACTING CUSTOMERS.</span></h1>
    <p class="lead">Tarvex Engineering offers insight and ingenuity to solve critical challenges safely.</p>
    <p class="intro-copy">Tarvex Engineering is an Australian consulting and engineering firm specialising in Command &amp; Control, Communications and Computer (C4) technologies for customers within Industry, Defence and Government Departments.</p>
    <p class="intro-copy">Tarvex Engineering provides engineering resources, speciality services and project delivery from concept to completion in areas including:</p>
    <ul class="capabilities">
      <li><svg width="11" height="11" viewBox="0 0 11 11"><circle cx="5.5" cy="5.5" r="4.8" fill="none" stroke="#f2e21a"/><path d="M3 5.6l1.8 1.8L8.2 3.8" fill="none" stroke="#f2e21a" stroke-width="1.3"/></svg>Command and Control (C2) system integration</li>
      <li><svg width="11" height="11" viewBox="0 0 11 11"><circle cx="5.5" cy="5.5" r="4.8" fill="none" stroke="#f2e21a"/><path d="M3 5.6l1.8 1.8L8.2 3.8" fill="none" stroke="#f2e21a" stroke-width="1.3"/></svg>Plain and Secure voice &amp; data TCP/IP communications</li>
      <li><svg width="11" height="11" viewBox="0 0 11 11"><circle cx="5.5" cy="5.5" r="4.8" fill="none" stroke="#f2e21a"/><path d="M3 5.6l1.8 1.8L8.2 3.8" fill="none" stroke="#f2e21a" stroke-width="1.3"/></svg>Acoustics, Noise, Shock and Vibration design, analysis and test</li>
      <li><svg width="11" height="11" viewBox="0 0 11 11"><circle cx="5.5" cy="5.5" r="4.8" fill="none" stroke="#f2e21a"/><path d="M3 5.6l1.8 1.8L8.2 3.8" fill="none" stroke="#f2e21a" stroke-width="1.3"/></svg>RF System Visualisation, Modelling and Analytics</li>
      <li><svg width="11" height="11" viewBox="0 0 11 11"><circle cx="5.5" cy="5.5" r="4.8" fill="none" stroke="#f2e21a"/><path d="M3 5.6l1.8 1.8L8.2 3.8" fill="none" stroke="#f2e21a" stroke-width="1.3"/></svg>Networked systems including VoIP, IPTV, CCTV and Videowall technologies</li>
      <li><svg width="11" height="11" viewBox="0 0 11 11"><circle cx="5.5" cy="5.5" r="4.8" fill="none" stroke="#f2e21a"/><path d="M3 5.6l1.8 1.8L8.2 3.8" fill="none" stroke="#f2e21a" stroke-width="1.3"/></svg>Logistics, Training and ongoing program support solutions</li>
    </ul>
    <div class="network-visual" role="img" aria-label="Illustration of networked computers, servers and mobile devices connected over a glowing blue world map"></div>
  </section>

  <section class="panel panel--services">
    <p class="services-intro">Tarvex Engineering staff have been in the forefront of major program deliveries to defence and commercial customers for decades. Our staff are leaders in their field and pioneers in the establishment of systematic approaches to the most complex problems.</p>
    <svg class="chart" width="300" height="150" viewBox="0 0 300 150" role="img" aria-label="Bar chart of service mix: Network Systems 40%, Communications Systems 35%, Command and Control Systems 20%, Sensor Systems 5%">
      <defs>
        <linearGradient id="barNet" x1="0" x2="1"><stop offset="0" stop-color="#2a8ee0"/><stop offset="1" stop-color="#1a5fb0"/></linearGradient>
        <linearGradient id="barComm" x1="0" x2="1"><stop offset="0" stop-color="#3a4fc4"/><stop offset="1" stop-color="#22309a"/></linearGradient>
        <linearGradient id="barCmd" x1="0" x2="1"><stop offset="0" stop-color="#6a3bb0"/><stop offset="1" stop-color="#46237e"/></linearGradient>
        <linearGradient id="barSensor" x1="0" x2="1"><stop offset="0" stop-color="#b44fb0"/><stop offset="1" stop-color="#86307f"/></linearGradient>
      </defs>
      <rect x="4" y="40" width="44" height="100" fill="url(#barNet)"/><ellipse cx="26" cy="140" rx="22" ry="6" fill="#1a5fb0"/><ellipse cx="26" cy="40" rx="22" ry="6" fill="#5fb0f0"/>
      <rect x="62" y="52" width="40" height="84" fill="url(#barComm)"/><ellipse cx="82" cy="136" rx="20" ry="5.5" fill="#22309a"/><ellipse cx="82" cy="52" rx="20" ry="5.5" fill="#5b6ee0"/>
      <rect x="118" y="88" width="34" height="44" fill="url(#barCmd)"/><ellipse cx="135" cy="132" rx="17" ry="5" fill="#46237e"/><ellipse cx="135" cy="88" rx="17" ry="5" fill="#8a5ad0"/>
      <rect x="168" y="120" width="30" height="8" fill="url(#barSensor)"/><ellipse cx="183" cy="128" rx="15" ry="4" fill="#86307f"/><ellipse cx="183" cy="120" rx="15" ry="4" fill="#d070cc"/>
      <g fill="none" stroke-width=".8">
        <path d="M26 34 V26 H80 L110 12 H200" stroke="#1e6fc4"/>
        <path d="M82 46 V38 H120 L150 24 H214" stroke="#2b3aa6"/>
        <path d="M135 82 V70 L165 40 H228" stroke="#5a2d9a"/>
        <path d="M183 116 V80 L205 56 H240" stroke="#a0399c"/>
      </g>
      <g font-family="Questrial, sans-serif" font-size="6.5">
        <text x="204" y="14" fill="#1e6fc4">Network Systems – 40%</text>
        <text x="218" y="26" fill="#2b3aa6">Comms Systems – 35%</text>
        <text x="230" y="42" fill="#5a2d9a">C2 Systems – 20%</text>
        <text x="244" y="58" fill="#a0399c">Sensors – 5%</text>
      </g>
    </svg>
    <div class="service-group">
      <h2 class="service-title service-title--network">Network Systems – 40%</h2>
      <ul class="service-list">
        <li>Defence Classified Networking</li>
        <li>Cryptographic Systems design</li>
        <li>High Speed Data Communications</li>
        <li>IP Voice Communications Systems Integration</li>
        <li>Information and Cybersecurity solutions</li>
      </ul>
    </div>
    <div class="service-group">
      <h2 class="service-title service-title--comms">Communications Systems – 35%</h2>
      <ul class="service-list">
        <li>Secure communications architecture</li>
        <li>Wideband Data Links and WIFI</li>
        <li>Microwave and Satellite Communications</li>
        <li>Custom/Speciality Antennas and RF Systems</li>
        <li>Anti-Jam Communications links</li>
      </ul>
    </div>
    <div class="service-group">
      <h2 class="service-title service-title--command">Command and Control Systems – 20%</h2>
      <ul class="service-list">
        <li>Human Factors design and development</li>
        <li>Command System integration</li>
        <li>UHD TV and Video Wall display design</li>
        <li>C2 Network integration</li>
      </ul>
    </div>
    <div class="service-group">
      <h2 class="service-title service-title--sensor">Sensor Systems – 5%</h2>
      <ul class="service-list">
        <li>Thermal monitoring</li>
        <li>Data Logging and Analysis</li>
        <li>IoT Sensor integration</li>
        <li>Shock/Vibration and Acoustics inspection and test services</li>
      </ul>
    </div>
  </section>

  <section class="panel panel--capability">
    <div class="tower-photo" role="img" aria-label="Photograph of a red and white telecommunications tower with radio antennas against a blue sky"></div>
    <svg class="capability-band" viewBox="0 0 360 384" preserveAspectRatio="none" aria-hidden="true">
      <defs>
        <linearGradient id="bandFill" x1="0" y1="0" x2="0" y2="1"><stop offset="0" stop-color="#2f58b8"/><stop offset="1" stop-color="#233f97"/></linearGradient>
      </defs>
      <path d="M0 60 Q180 -10 360 30 V384 H0 Z" fill="#ffffff"/>
      <path d="M0 70 Q180 2 360 40 V384 H0 Z" fill="url(#bandFill)"/>
    </svg>
    <div class="capability-copy">
      <p>At Tarvex Engineering we have a broad mix of capabilities, including abilities in the areas of networking, communications, C2 system integration with sensor and communications systems. Our staff have supported the largest telecommunications networks in Australia and aided defence in building realtime, secure data networks for communications and data sharing. We have enabled communications across multiple platforms types including aircraft, rail, ship and vehicle platforms that operate reliably under extreme environmental conditions.</p>
      <p>At Tarvex Engineering, we are committed to delivering value to all our customers and end users in a manner that inspires.</p>
    </div>
  </section>

</main>
</body>
</html>
```